New Zealand Marlborough Sauvignon Blanc wine packaging design

We need packaging design for our new wine brand, Dunmore Vale. The wine is a New Zealand Marlborough Sauvignon Blanc. We would like the packaging will portray elegance and style with an understated label. We are looking for a label that portrays the elegance of the French Riviera. The label should be round or pill shaped.
Updates

Industry/Entity Type

Wine

Font styles to use
Serif
Sans Serif

Requirements
Must have
• The words in order of importance: Dunmore Vale, Sauvignon Blanc, Marlborough, New Zealand. It should be fit to the bottle posted in the links
Nice to have
• a pill shape or circular shape
Should not have
• Illustrations of wine bottles, wine glasses, or grapes

```html
<!DOCTYPE html>
<html lang="en">
<head>
<meta charset="utf-8">
<title>Dunmore Vale — Sauvignon Blanc Label</title>
<link rel="stylesheet" href="https://fonts.googleapis.com/css2?family=Mrs+Saint+Delafield&family=Raleway:wght@200;300&display=swap">
<style>
  :root {
    --bronze: #98694d;
    --paper: #ffffff;
  }
  html, body {
    margin: 0;
    padding: 0;
    width: 1200px;
    height: 675px;
    overflow: hidden;
    background: var(--paper);
  }
  .canvas {
    position: relative;
    width: 1200px;
    height: 675px;
    background: var(--paper);
  }
  .label-ring {
    position: absolute;
    left: 0;
    top: 0;
  }
  .label-text {
    position: absolute;
    left: 0;
    top: 0;
    width: 1200px;
    height: 675px;
    display: flex;
    flex-direction: column;
    align-items: center;
    justify-content: center;
    color: var(--bronze);
  }
  .brand-name {
    font-family: "Mrs Saint Delafield", cursive;
    font-weight: 400;
    font-size: 58px;
    line-height: 1;
    margin: 0;
    letter-spacing: 1px;
  }
  .divider {
    width: 28px;
    height: 1px;
    background: var(--bronze);
    margin: 10px 0 14px;
  }
  .varietal {
    font-family: "Raleway", sans-serif;
    font-weight: 200;
    font-size: 16px;
    letter-spacing: 13px;
    margin: 0 0 0 13px;
  }
  .region {
    font-family: "Raleway", sans-serif;
    font-weight: 300;
    font-size: 11px;
    letter-spacing: 0;
    margin: 28px 0 0;
  }
</style>
</head>
<body>
  <main class="canvas">
    <svg class="label-ring" width="1200" height="675" viewBox="0 0 1200 675" aria-hidden="true">
      <circle cx="600" cy="337.5" r="222" fill="none" stroke="var(--bronze)" stroke-width="30"/>
    </svg>
    <div class="label-text">
      <h1 class="brand-name">Dunmore Vale</h1>
      <div class="divider"></div>
      <p class="varietal">SAUVIGNON BLANC</p>
      <p class="region">MARLBOROUGH, NEW ZEALAND</p>
    </div>
  </main>
</body>
</html>
```